Torvane Halbridge

Looking for modern business cards.
Clean contemporary design.
Similar to this.
https://www.plumvexa-search.example/imgres?imgurl=https%3A%2F%2Fimg.quorlint-cdn.example%2Fsleek_dark_metal_card_design_540.jpg&imgrefurl=https%3A%2F%2Fwww.quorlint-prints.example%2Fsleek_dark_metal_card_design-918273645501928374&q=modern%20business%20cards

But I'd like the blue to look metallic.

Business

```html
<!DOCTYPE html>
<html lang="en">
<head>
<meta charset="utf-8">
<title>Torvane Halbridge – Business Card</title>
<link href="https://fonts.googleapis.com/css2?family=Roboto:wght@400;500&family=Roboto+Condensed:wght@400;700&display=swap" rel="stylesheet">
<style>
  :root {
    --canvas: #e2e2e2;
    --paper: #f3f3f3;
    --navy-teal: #24566b;
    --navy-dark: #173d4d;
    --navy-light: #3f7d94;
    --navy-sheen: #7fb0c2;
    --bright-blue: #2a9bbf;
    --blue-dark: #1c7594;
    --blue-sheen: #8fd3e8;
    --accent-red: #e8452c;
    --text-grey: #4f4f4f;
    --divider: #9a9a9a;
    --white: #ffffff;
    --metal-navy: linear-gradient(115deg,
      var(--navy-dark) 0%, var(--navy-teal) 22%, var(--navy-light) 38%,
      var(--navy-sheen) 47%, var(--navy-light) 55%, var(--navy-teal) 72%,
      var(--navy-dark) 88%, var(--navy-teal) 100%);
  }
  * { box-sizing: border-box; margin: 0; padding: 0; }
  html, body {
    width: 1200px; height: 960px; overflow: hidden;
    background: var(--canvas);
    font-family: "Roboto", Arial, sans-serif;
  }
  .canvas { position: relative; width: 1200px; height: 960px; }

  .card { position: absolute; width: 600px; height: 343px; overflow: hidden; }
  .card-front { left: 314px; top: 113px; background: var(--paper); }
  .card-back { left: 311px; top: 472px; background: var(--metal-navy); }
  .card-back::after {
    content: ""; position: absolute; inset: 0;
    background: repeating-linear-gradient(90deg,
      rgba(255,255,255,0.03) 0px, rgba(255,255,255,0.03) 1px,
      rgba(0,0,0,0.03) 2px, rgba(0,0,0,0.03) 3px);
    pointer-events: none;
  }

  .brand-name {
    position: absolute; left: 46px; top: 168px;
    font-family: "Roboto", Arial, sans-serif; font-weight: 500;
    font-size: 23px; color: var(--navy-teal); letter-spacing: -0.2px;
    display: flex; align-items: center; gap: 9px;
  }
  .brand-dot { width: 8px; height: 8px; border-radius: 50%; background: var(--accent-red); }

  .divider {
    position: absolute; left: 323px; top: 62px; width: 1.5px; height: 222px;
    background: linear-gradient(to bottom, transparent, var(--divider) 15%, var(--divider) 85%, transparent);
  }

  .contact { position: absolute; left: 357px; top: 71px; color: var(--text-grey); }
  .person-name {
    font-family: "Roboto Condensed", Arial, sans-serif; font-weight: 700;
    font-size: 21px; color: var(--navy-teal); line-height: 26px;
  }
  .person-title {
    font-family: "Roboto Condensed", Arial, sans-serif; font-weight: 400;
    font-size: 16px; color: var(--bright-blue); line-height: 20px;
  }
  .address { margin-top: 9px; font-size: 15px; line-height: 19px; }
  .contact-list { list-style: none; margin-top: 10px; font-size: 15px; }
  .contact-list li { display: flex; align-items: center; height: 19px; gap: 8px; }
  .contact-list svg { width: 14px; height: 14px; fill: var(--navy-teal); flex: none; }

  .front-band { position: absolute; left: 0; bottom: 0; width: 600px; height: 13px; }

  .back-brand {
    position: absolute; left: 0; top: 130px; width: 100%; z-index: 1;
    display: flex; justify-content: center; align-items: center; gap: 12px;
    font-family: "Roboto", Arial, sans-serif; font-weight: 500;
    font-size: 30px; color: var(--white);
  }
  .back-brand .brand-dot { width: 12px; height: 12px; }
  .back-url {
    position: absolute; left: 0; top: 289px; width: 100%; text-align: center; z-index: 1;
    font-size: 14px; letter-spacing: 2.6px; color: var(--white);
  }
</style>
</head>
<body>
<main class="canvas">
  <section class="card card-front" aria-label="Card front">
    <div class="brand-name"><span>Torvane Halbridge</span><span class="brand-dot"></span></div>
    <div class="divider"></div>
    <div class="contact">
      <h1 class="person-name">ELRIC DANMOOR</h1>
      <p class="person-title">CEO/FOUNDER</p>
      <p class="address">4216 Quillan Row<br>Fernhollow, Vestry 50821</p>
      <ul class="contact-list">
        <li><svg viewBox="0 0 16 16" aria-hidden="true"><path d="M3.6 1.2 6 3.6 4.7 5.6c.9 2.2 2.6 3.9 4.8 4.8l2-1.3 2.4 2.4-1.5 2.3C7.6 14 2.1 8.5 1.3 3.7z"/></svg>555 014 2738</li>
        <li><svg viewBox="0 0 16 16" aria-hidden="true"><path d="M4.5 1h7v14h-7zM6 2.5v9.5h4V2.5zm1.5 10.5v1h1v-1z"/></svg>555 019 6482</li>
        <li><svg viewBox="0 0 16 16" aria-hidden="true"><path d="M4 1h8v4H4zM1 6h14v7h-3v2H4v-2H1zm4 4v4h6v-4z"/></svg>555 017 3094</li>
        <li><svg viewBox="0 0 16 16" aria-hidden="true"><path d="M1 4h14v9H1zm1.4 1 5.6 4.2L13.6 5z"/></svg>elric@torvane.example</li>
        <li><svg viewBox="0 0 16 16" aria-hidden="true"><path d="M8 1a7 7 0 1 0 0 14A7 7 0 0 0 8 1zm-1 2.2c-.4 1.3 0 2.3-1.3 2.6-1 .2-1.4 1.2-.6 2 .9.8 2 .4 2.3 1.7.2 1-.4 2.2-.2 3.1A5.6 5.6 0 0 1 7 3.2zm3.5 1c.8.7.2 1.8-.6 2.2-.8.5-.2 1.4.6 1.3 1-.1 1.6.4 1.8 1.2a5.6 5.6 0 0 0-1.8-4.7z"/></svg>www.torvane.example</li>
      </ul>
    </div>
    <svg class="front-band" viewBox="0 0 600 13" preserveAspectRatio="none" aria-hidden="true">
      <defs>
        <linearGradient id="metal-navy-band" x1="0" y1="0" x2="1" y2="0">
          <stop offset="0" stop-color="#173d4d"/>
          <stop offset="0.3" stop-color="#24566b"/>
          <stop offset="0.5" stop-color="#6f9fb2"/>
          <stop offset="0.7" stop-color="#24566b"/>
          <stop offset="1" stop-color="#173d4d"/>
        </linearGradient>
        <linearGradient id="metal-blue-band" x1="0" y1="0" x2="1" y2="0">
          <stop offset="0" stop-color="#1c7594"/>
          <stop offset="0.4" stop-color="#2a9bbf"/>
          <stop offset="0.55" stop-color="#8fd3e8"/>
          <stop offset="0.75" stop-color="#2a9bbf"/>
          <stop offset="1" stop-color="#1c7594"/>
        </linearGradient>
        <linearGradient id="band-gloss" x1="0" y1="0" x2="0" y2="1">
          <stop offset="0" stop-color="#ffffff" stop-opacity="0.28"/>
          <stop offset="0.5" stop-color="#ffffff" stop-opacity="0"/>
          <stop offset="1" stop-color="#000000" stop-opacity="0.15"/>
        </linearGradient>
      </defs>
      <polygon points="0,0 393,0 389,13 0,13" fill="url(#metal-navy-band)"/>
      <polygon points="396,0 600,0 600,13 392,13" fill="url(#metal-blue-band)"/>
      <rect x="0" y="0" width="600" height="13" fill="url(#band-gloss)"/>
    </svg>
  </section>

  <section class="card card-back" aria-label="Card back">
    <div class="back-brand"><span>Torvane Halbridge</span><span class="brand-dot"></span></div>
    <p class="back-url">www.torvanehalbridge.example</p>
  </section>
</main>
</body>
</html>
```